Plakate für ein Fest
Zielgruppe
Das Kessner Park ist ein Gewerbepark mit unterschiedlichen Mietern von Handwerker über Musiker bis hin zu Vermögensberatung. Wir veranstalten ein Fest für unsere Mieter und möchten dieses Plakat als Einladung nutzen.
Aufgabenstellung
Hintergrund schwarz, Logo verwenden
Get together
BBQ & Cocktails im Kessner Park
am 13.10.2023 ab 18 Uhr
Logo Band wild pebbles
Kinderbereich
Wir freuen uns darauf, alle Mieter mit Familien begrüßen zu dürfen! Auch an die Kleinen haben wir gedacht.

```html
<!DOCTYPE html>
<html lang="de">
<head>
<meta charset="utf-8">
<title>Get Together – BBQ &amp; Cocktails im Kessner Park</title>
<link rel="stylesheet" href="https://fonts.googleapis.com/css2?family=Bebas+Neue&family=Inter+Tight:wght@500;700&display=swap">
<style>
  :root {
    --page-bg: #e8e9eb;
    --poster-black: #000000;
    --lime: #dfda4b;
    --purple: #7b5ea8;
    --green: #5a8f45;
    --kids-blue: #7aa5b9;
    --dot-green: #123f28;
    --white: #ffffff;
    --ink: #111111;
  }
  html, body {
    margin: 0;
    width: 1000px;
    height: 1200px;
    overflow: hidden;
    background: var(--page-bg);
  }
  .poster {
    position: absolute;
    left: 96px;
    top: 30px;
    width: 807px;
    height: 1140px;
    display: block;
  }
  .display { font-family: "Bebas Neue", "Oswald", sans-serif; }
  .sans { font-family: "Inter Tight", "Helvetica Neue", Arial, sans-serif; }
  .time { font-weight: 500; font-size: 72px; fill: var(--ink); }
  .date { font-size: 112px; fill: var(--ink); }
  .headline { fill: var(--white); }
  .outlined { fill: var(--white); stroke: var(--ink); stroke-width: 5px; paint-order: stroke; }
  .band-name { font-weight: 700; font-size: 62px; fill: var(--white); }
  .invite { font-weight: 700; font-size: 36px; fill: var(--white); }
  .host-name { font-weight: 700; font-size: 70px; fill: var(--white); }
</style>
</head>
<body>
<svg class="poster" viewBox="0 0 1053 1488" xmlns="http://www.w3.org/2000/svg">
  <defs>
    <clipPath id="poster-clip"><rect width="1053" height="1488"/></clipPath>
    <linearGradient id="grill-tone" x1="0" y1="0" x2="0" y2="1">
      <stop offset="0" stop-color="#e3001b"/>
      <stop offset="0.45" stop-color="#8a8a8a"/>
      <stop offset="1" stop-color="#5e5e5e"/>
    </linearGradient>
    <linearGradient id="cocktail-tone" x1="0" y1="0" x2="0" y2="1">
      <stop offset="0" stop-color="#f5c04a"/>
      <stop offset="0.45" stop-color="#fbe07c"/>
      <stop offset="1" stop-color="#5fc0e8"/>
    </linearGradient>
  </defs>

  <g clip-path="url(#poster-clip)">
    <rect class="poster-bg" width="1053" height="1488" fill="var(--poster-black)"/>

    <!-- dot grid areas -->
    <rect role="img" aria-label="Grünes Punktraster" x="870" y="0" width="183" height="286" fill="var(--dot-green)"/>
    <rect role="img" aria-label="Grünes Punktraster" x="2" y="1331" width="210" height="157" fill="var(--dot-green)"/>

    <!-- date block -->
    <rect class="date-block" x="64" y="0" width="853" height="247" fill="var(--lime)"/>
    <text class="sans time" x="97" y="101" textLength="388" lengthAdjust="spacingAndGlyphs">AB 18.00 UHR</text>
    <text class="display date" x="97" y="214" textLength="735" lengthAdjust="spacingAndGlyphs">FREITAG 13.10.2023</text>

    <!-- headline bands -->
    <g class="band band--purple">
      <polygon points="197,268 885,308 875,499 187,459" fill="var(--purple)"/>
      <text class="display headline" x="536" y="444" font-size="178" text-anchor="middle"
            textLength="638" lengthAdjust="spacingAndGlyphs" transform="rotate(3.3 536 383)">GET TOGETHER</text>
    </g>

    <g class="band band--lime">
      <polygon points="62,526 955,482 965,696 64,733" fill="var(--lime)"/>
      <text class="display outlined" x="514" y="674" font-size="192" text-anchor="middle"
            textLength="835" lengthAdjust="spacingAndGlyphs" transform="rotate(-2.8 514 606)">BBQ &amp; COCKTAILS</text>
    </g>

    <g class="band band--green">
      <polygon points="219,726 905,744 900,903 214,883" fill="var(--green)"/>
      <text class="display headline" x="559" y="866" font-size="145" text-anchor="middle"
            textLength="609" lengthAdjust="spacingAndGlyphs" transform="rotate(1.5 559 815)">IM KESSNER PARK</text>
    </g>

    <!-- grill illustration area -->
    <rect role="img" aria-label="Illustration eines Kugelgrills mit geöffnetem roten Deckel und Würstchen" x="0" y="710" width="222" height="330" rx="6" fill="url(#grill-tone)"/>

    <!-- kids area badge -->
    <g class="kids-badge">
      <circle cx="167" cy="1239" r="171" fill="var(--kids-blue)"/>
      <g transform="rotate(-12 150 1240)">
        <text class="display outlined" x="150" y="1225" font-size="100" text-anchor="middle">KINDER</text>
        <text class="display outlined" x="162" y="1318" font-size="100" text-anchor="middle">BEREICH</text>
      </g>
    </g>

    <!-- band name -->
    <text class="sans band-name" x="267" y="975">wild pebbles</text>

    <!-- invitation text -->
    <g class="invite-copy sans">
      <text class="invite" x="267" y="1056" textLength="447" lengthAdjust="spacingAndGlyphs">Wir freuen uns darauf, alle</text>
      <text class="invite" x="320" y="1108" textLength="502" lengthAdjust="spacingAndGlyphs">Mieter mit Familien begrüßen</text>
      <text class="invite" x="364" y="1160" textLength="378" lengthAdjust="spacingAndGlyphs">zu dürfen! Auch an die</text>
      <text class="invite" x="381" y="1212" textLength="308" lengthAdjust="spacingAndGlyphs">Kleinen haben wir</text>
      <text class="invite" x="386" y="1264" textLength="151" lengthAdjust="spacingAndGlyphs">gedacht.</text>
    </g>

    <!-- host name -->
    <g class="host">
      <rect x="340" y="1350" width="78" height="78" fill="var(--green)"/>
      <text class="sans host-name" x="480" y="1372" textLength="320" lengthAdjust="spacingAndGlyphs">KESSNER</text>
      <text class="sans host-name" x="480" y="1434">PARK</text>
    </g>

    <!-- cocktail illustration area -->
    <rect role="img" aria-label="Illustration eines Cocktailglases mit Strohhalm und Schirmchen" x="842" y="970" width="211" height="470" rx="6" fill="url(#cocktail-tone)"/>
  </g>
</svg>
</body>
</html>
```